Tallow Crest - Facebook Cover Photo & Photo Icon Design

We’re looking for a Facebook Cover Photo and Profile Icon design for Tallow Crest, a leading Residential Real Estate brand under Kestmore Property Agents, based in Capalaba and Alexandra Hills, Queensland, Australia.

This design will represent my professional real estate profile and needs to be bold, clean, and on-brand.

Deliverables:

Facebook Cover Photo (820 x 312 px, optimized for mobile + desktop)

Facebook Profile Icon (1:1 ratio, minimum 320 x 320 px)

Design Guidelines:

1. Must Include:

The Tallow Crest logo (provided after project start)

Use of the Kestmore Property Agents brand colour palette (will be supplied)

Clear connection to residential real estate

2. Optional but Preferred:

A local photo or skyline of Capalaba or Alexandra Hills in QLD (bonus points for this)

Space for a short tagline like:
“Selling Faster. Selling Smarter. Selling Kestmore.”
(Optional tagline – open to variations if it improves layout/design)

3. Style & Feel:

Professional yet personable

Clean, modern aesthetic

Subtle touches of fun or personality are welcome

Layout must work well when overlaid by Facebook UI elements (like profile photo & call-to-action buttons)

Who I Am:
I'm a well-known residential real estate agent in the Redlands area, known for high-energy campaigns, premium video marketing, and a results-driven approach. My brand is fun, fresh, and high-performing — just like the real estate campaigns I run.

Files to be Provided (after selection):

Tallow Crest logo in high-res

Brand colour palette / style reference

Optional photo references if local imagery is not sourced by designer

Final Notes:

Make sure all text is legible on mobile and desktop

Original, layered design files must be delivered (PSD or AI preferred)

Bonus points if it feels uniquely “Bayside Queensland” while maintaining a national-level professional polish

Target Market(s)

Alexandra Hills, Capalaba & Sheldon

Industry/Entity Type

Real Estate

Colors
0054AA
0677BA
7BADD7
CADEEF
E8F1F8

Requirements
Must have
• Headshot, Mobile Number 0417 962 085, Suburbs - Alexandra Hills, Capalaba & Sheldon
Nice to have
• White, Crisp & Professional. Bottom Banner with Suburb List. Specialising in Alexandra Hills, Capalaba & Sheldon

```html
<!DOCTYPE html>
<html lang="en">
<head>
<meta charset="utf-8">
<title>Tallow Crest – Facebook Cover &amp; Profile Icon</title>
<link rel="stylesheet" href="https://fonts.googleapis.com/css2?family=Poppins:wght@400;500&display=swap">
<style>
  :root {
    --stage-grey: #8e8e8e;
    --cover-navy: #00135b;
    --skyline-tone: 28, 44, 110;
    --accent-gold: #f8b05a;
    --text-white: #ffffff;
    --band-navy: #0a1f6e;
    --headshot-light: #7badd7;
    --headshot-dark: #0677ba;
    --icon-tan: #d8a96c;
    --icon-ink: #0d1a56;
    --icon-border: #ffffff;
  }
  * { margin: 0; padding: 0; box-sizing: border-box; }
  html, body {
    width: 1200px;
    height: 665px;
    overflow: hidden;
    background: var(--stage-grey);
  }
  .canvas {
    position: relative;
    width: 1200px;
    height: 665px;
    background: var(--stage-grey);
    font-family: "Poppins", sans-serif;
  }
  .cover {
    position: absolute;
    left: 113px;
    top: 113px;
    width: 974px;
    height: 371px;
    background: var(--cover-navy);
    overflow: hidden;
  }
  .cover__skyline {
    position: absolute;
    inset: 0;
    background: linear-gradient(180deg,
      rgba(var(--skyline-tone), 0) 0%,
      rgba(var(--skyline-tone), 0.5) 35%,
      rgba(var(--skyline-tone), 0.7) 100%);
  }
  .cover__headshot {
    position: absolute;
    left: 88px;
    top: 36px;
    width: 170px;
    height: 170px;
    border-radius: 50%;
    border: 3px solid var(--accent-gold);
    background: radial-gradient(circle at 50% 40%, var(--headshot-light), var(--headshot-dark));
  }
  .cover__tagline {
    position: absolute;
    left: 380px;
    top: 80px;
    list-style: none;
    font-weight: 500;
    font-size: 54px;
    line-height: 70px;
    letter-spacing: 0.3px;
    text-transform: uppercase;
  }
  .tagline__line--gold { color: var(--accent-gold); }
  .tagline__line--white { color: var(--text-white); }
  .cover__band {
    position: absolute;
    left: 0;
    right: 0;
    bottom: 0;
    height: 52px;
    background: var(--band-navy);
    border-top: 2px solid var(--accent-gold);
    display: flex;
    align-items: center;
    justify-content: space-between;
    padding: 0 36px 0 380px;
    color: var(--text-white);
    font-weight: 400;
    font-size: 19px;
  }
  .band__item {
    display: flex;
    align-items: center;
    gap: 10px;
  }
  .band__icon {
    width: 22px;
    height: 22px;
    fill: var(--accent-gold);
    flex: none;
  }
  .band__phone { font-weight: 500; letter-spacing: 0.5px; }
  .profile-icon {
    position: absolute;
    left: 176px;
    top: 339px;
    width: 220px;
    height: 220px;
    background: var(--icon-tan);
    border: 3px solid var(--icon-border);
    border-radius: 3px;
    display: flex;
    align-items: center;
    justify-content: center;
  }
  .profile-icon__name {
    color: var(--icon-ink);
    font-weight: 400;
    font-size: 36px;
    line-height: 42px;
    letter-spacing: 3px;
    text-transform: uppercase;
    text-align: center;
  }
</style>
</head>
<body>
  <main class="canvas">
    <section class="cover" aria-label="Facebook cover photo">
      <div class="cover__skyline" role="img" aria-label="Faint city skyline silhouette across the cover"></div>
      <div class="cover__headshot" role="img" aria-label="Agent headshot"></div>
      <ul class="cover__tagline">
        <li class="tagline__line--gold">Selling Faster.</li>
        <li class="tagline__line--white">Selling Smarter.</li>
        <li class="tagline__line--gold">Selling Kestmore.</li>
      </ul>
      <div class="cover__band">
        <p class="band__item">
          <svg class="band__icon" viewBox="0 0 24 24" aria-hidden="true"><path d="M12 3 2 11.5h3V21h5.5v-6h3v6H19v-9.5h3z"/></svg>
          <span>Alexandra Hills · Capalaba · Sheldon</span>
        </p>
        <p class="band__item">
          <svg class="band__icon" viewBox="0 0 24 24" aria-hidden="true"><path d="M6.6 10.8a15.1 15.1 0 0 0 6.6 6.6l2.2-2.2a1 1 0 0 1 1-.25 11.4 11.4 0 0 0 3.6.57 1 1 0 0 1 1 1V20a1 1 0 0 1-1 1A17 17 0 0 1 3 4a1 1 0 0 1 1-1h3.5a1 1 0 0 1 1 1c0 1.25.2 2.45.57 3.6a1 1 0 0 1-.25 1z"/></svg>
          <span class="band__phone">0417 962 085</span>
        </p>
      </div>
    </section>
    <aside class="profile-icon" aria-label="Facebook profile icon">
      <p class="profile-icon__name">Tallow<br>Crest</p>
    </aside>
  </main>
</body>
</html>
```